SkyvoTrade - where frequent flyers can cash out their airline miles

SkyvoTrade enable the trade of airline miles between individuals. Our landing page which I want to redesign should refer to individuals who have miles in airline loyalty programs and would like to sell them with our platform

I would like to get a landing page design with a look and feel much more advanced and appealing then the one we currently have.

Page should include the information and fields in our current landing page but should be more professional and include except for the current two partner's logos and our logo of course, also the attached banner of staynestly.example with a link to staynestly.example with our affiliate code.

Audience of our web page is business men and heavy travellers therefore, page should reflect professionalism and should be business wise. There could be something that has to do with airplanes and money in terms of the background and pictures shows.

Additional text (on top of the short description at skyvotrade.example is -
"
SkyvoTrade™ converts frequent flyers' accumulated miles to exceptionally low-priced flight tickets. It serves as an online trading platform for sellers of miles and buyers of flight tickets, offering airline customers a fully automated process whereby flight tickets are created out of loyalty club miles.
"

Our web site as a reference is www.skyvotrade.example

Target Market(s)

Business men who are heavily travellers

Industry/Entity Type

Travel Industry

Number of Pages Required

1 page

Font styles to use
Sans Serif

Colors
85acd3
0255a3

Requirements
Must have
• Our logo and the 3 logos mentioned at the description. It should have on the top the look & Feel that it currently has on our landing page - www.skyvotrade.example
Nice to have
• I would like people entering the web page to love it and for them to leave the relevant details so we get back to them
Should not have
• Not too many texts or images. Don't want people to scroll down too much if at all

```html
<!DOCTYPE html>
<html lang="en">
<head>
<meta charset="utf-8">
<title>SkyvoTrade – Sell Your Miles</title>
<link href="https://fonts.googleapis.com/css2?family=Arimo:wght@400;700&family=Open+Sans:wght@400;600&family=Raleway:wght@400;500;600&display=swap" rel="stylesheet">
<style>
  :root {
    --brand-deep: #0255a3;
    --brand-soft: #85acd3;
    --brand-mid: #2a6cb8;
    --sky-light: #dbe9f7;
    --sky-mid: #7fb0e0;
    --sky-deep: #1f66c2;
    --ink: #3a3a3a;
    --muted: #6b6b6b;
    --rule: #cfcfcf;
    --white: #ffffff;
    --field-text: #666;
  }
  * { box-sizing: border-box; margin: 0; padding: 0; }
  html, body { width: 1099px; height: 1200px; overflow: hidden; background: var(--white); }
  body { position: relative; font-family: "Open Sans", sans-serif; color: var(--ink); }

  .hero { position: absolute; left: 0; top: 0; width: 1099px; height: 534px; overflow: hidden; }
  .hero-photo { position: absolute; inset: 0;
    background: radial-gradient(ellipse at 8% 10%, #ffffff 0%, #eaf3fb 18%, transparent 45%),
                linear-gradient(160deg, var(--sky-light) 0%, var(--sky-mid) 45%, var(--sky-deep) 100%); }

  .brand { position: absolute; left: 167px; top: 46px; }
  .brand-name { font-family: "Arimo", sans-serif; font-weight: 700; font-size: 32px; color: #111; letter-spacing: -0.5px; line-height: 1; }

  .main-nav { position: absolute; top: 55px; left: 0; font-family: "Arimo", sans-serif; font-size: 16px; color: var(--white); }
  .main-nav a { position: absolute; color: var(--white); text-decoration: none; white-space: nowrap; }

  .hero-title { position: absolute; left: 165px; top: 206px; font-family: "Arimo", sans-serif; font-weight: 700; font-size: 38px; color: var(--brand-deep); line-height: 1; letter-spacing: 0.5px; }
  .hero-subtitle { position: absolute; left: 165px; top: 258px; font-family: "Arimo", sans-serif; font-weight: 700; font-size: 30px; color: var(--brand-mid); line-height: 1; opacity: 0.85; }
  .hero-copy { position: absolute; left: 165px; top: 300px; width: 420px; font-size: 10.2px; line-height: 16.4px; color: var(--brand-deep); }
  .btn-dark { position: absolute; left: 166px; top: 364px; width: 103px; height: 32px; background: linear-gradient(#0e5fb0, #003f86); color: var(--white); font-size: 12px; display: flex; align-items: center; justify-content: center; }

  .lead-form { position: absolute; left: 677px; top: 151px; width: 254px; height: 275px; background: var(--brand-deep); border-radius: 3px; overflow: hidden; }
  .lead-form::before { content: ""; position: absolute; left: -20px; top: -70px; width: 300px; height: 115px; background: linear-gradient(#4f88c7, #2d6db5); border-radius: 0 0 60% 40%; }
  .form-title { position: absolute; left: 24px; top: 14px; font-family: "Raleway", sans-serif; font-size: 21px; color: var(--white); }
  .field { position: absolute; left: 23px; width: 213px; height: 26px; background: var(--white); border: 1px solid #c9d6e4; font-size: 9.5px; color: var(--field-text); padding-left: 10px; display: flex; align-items: center; }
  .field-half { width: 104px; }
  .btn-next { position: absolute; left: 24px; top: 225px; width: 213px; height: 31px; background: linear-gradient(#8fb4dc, #5d8fc8); color: var(--white); font-size: 13px; display: flex; align-items: center; justify-content: center; }

  .slider-dots { position: absolute; left: 512px; top: 501px; display: flex; gap: 3px; }
  .slider-dots span { width: 15px; height: 15px; border-radius: 50%; background: var(--white); }
  .slider-dots .active { background: var(--brand-deep); border: 3px solid var(--white); }

  .welcome { position: absolute; left: 0; top: 575px; width: 1099px; text-align: center; }
  .section-title { font-family: "Raleway", sans-serif; font-weight: 400; font-size: 29px; color: #333; display: flex; align-items: center; justify-content: center; gap: 10px; }
  .section-title::before, .section-title::after { content: ""; width: 157px; height: 1px; background: var(--rule); }
  .welcome-copy { margin: 14px auto 0; width: 740px; font-size: 10.4px; line-height: 20.4px; color: var(--muted); }

  .features-art { position: absolute; left: 354px; top: 690px; width: 394px; height: 140px; background: radial-gradient(ellipse, rgba(200,200,200,0.18), transparent 70%); }
  .feature { position: absolute; top: 719px; width: 220px; text-align: center; }
  .feature-icon { width: 96px; height: 96px; margin: 0 auto; border: 3px solid #7ea4d1; border-radius: 50%; background: var(--white); display: flex; align-items: center; justify-content: center; }
  .feature-title { margin-top: 12px; font-family: "Raleway", sans-serif; font-weight: 600; font-size: 17px; color: var(--brand-deep); }
  .feature-copy { margin-top: 7px; font-size: 10px; line-height: 17px; color: var(--muted); padding: 0 12px; }
  .btn-light { display: inline-flex; margin-top: 13px; width: 88px; height: 27px; align-items: center; justify-content: center; background: linear-gradient(#86abd4, #5c8ac3); color: var(--white); font-size: 10.5px; }

  .promo-banner { position: absolute; left: 158px; top: 1028px; width: 487px; height: 59px; overflow: hidden; }
  .promo-photo { position: absolute; left: 0; top: 0; width: 365px; height: 59px; background: linear-gradient(90deg, #bfe3f4 0%, #8fd0e6 40%, #e8dcc0 75%, #c89a6b 100%); }
  .promo-side { position: absolute; left: 365px; top: 0; width: 122px; height: 59px; background: #153f82; }
  .promo-head { position: absolute; left: 20px; top: 12px; font-family: "Open Sans", sans-serif; font-weight: 600; font-size: 16px; color: #0c2f66; }
  .promo-sub { position: absolute; left: 20px; top: 33px; font-size: 11px; color: var(--white); font-weight: 600; }
  .promo-brand { position: absolute; left: 14px; top: 8px; font-weight: 600; font-size: 12px; color: var(--white); }
  .promo-btn { position: absolute; left: 14px; top: 29px; width: 60px; height: 18px; border: 1px solid var(--white); background: #1d6fd1; color: var(--white); font-size: 9px; display: flex; align-items: center; justify-content: center; }

  .partners { position: absolute; left: 690px; top: 1030px; display: flex; align-items: center; gap: 14px; }
  .partner { display: flex; align-items: center; gap: 6px; font-family: "Open Sans", sans-serif; font-size: 14px; color: #3d4a57; }
  .partner-mark { width: 40px; height: 48px; background: #44596b; border-radius: 4px; }
  .partner-red { color: #c8202a; font-weight: 600; }

  .site-footer { position: absolute; left: 0; top: 1145px; width: 1099px; height: 55px; background: linear-gradient(#9bbbe0, var(--brand-soft)); }
  .copyright { position: absolute; left: 169px; top: 19px; font-size: 10.5px; color: var(--white); }
  .social { position: absolute; left: 824px; top: 10px; display: flex; gap: 2px; }
  .social span { width: 26px; height: 26px; border: 1.5px solid var(--white); border-radius: 50%; }
</style>
</head>
<body>

<header class="hero">
  <div class="hero-photo" role="img" aria-label="Passenger jet flying above bright clouds in a blue sky"></div>

  <div class="brand">
    <span class="brand-name">SkyvoTrade</span>
  </div>

  <nav class="main-nav">
    <a style="left:446px">About Us</a>
    <a style="left:549px">Sell Miles</a>
    <a style="left:656px">Services</a>
    <a style="left:754px">Resources</a>
    <a style="left:866px">Support</a>
  </nav>

  <h1 class="hero-title">SKYVOTRADE CONVERTS</h1>
  <h2 class="hero-subtitle">FREQUENT FLYERS</h2>
  <p class="hero-copy">accumulated miles to exceptionally low-priced flight tickets. It serves as an online trading platform for sellers of miles and buyers of flight tickets, offering airline customers a fully automated process whereby flight tickets are created out of loyalty club miles</p>
  <a class="btn-dark">Learn More</a>

  <form class="lead-form">
    <div class="form-title">Sell Your Miles</div>
    <div class="field" style="top:61px">First Name</div>
    <div class="field" style="top:94px">Last Name</div>
    <div class="field" style="top:127px">Email</div>
    <div class="field" style="top:160px">Phone</div>
    <div class="field field-half" style="top:193px">Airlines Detail</div>
    <div class="field field-half" style="top:193px;left:132px">Amount of miles</div>
    <div class="btn-next">Next Step</div>
  </form>

  <div class="slider-dots"><span class="active"></span><span></span><span></span><span></span></div>
</header>

<section class="welcome">
  <h2 class="section-title">Welcome to SkyvoTrade Mainapge</h2>
  <p class="welcome-copy">Vivamus porttitor purus nisi eleifend libero a tempus libero lectus feugiat felis Morbi diam mauris viverra in gravida eu mattis in ante Morbi eget arcu Morbi porta libero id ullamcorper nonummy nibh ligula pulvinar metus eget consectetuer augue nisi quis lacus Ut ac mi quis lacus mollis aliquam Curabitur iaculis tempus eros Curabitur vel mi sit amet magna malesuada ultricetis at cursus magna nisl nec elit vm</p>
</section>

<div class="features-art" role="img" aria-label="Faint line drawing of an airliner behind the service icons"></div>

<article class="feature" style="left:202px">
  <div class="feature-icon">
    <svg width="60" height="50" viewBox="0 0 60 50"><circle cx="30" cy="25" r="18" fill="#0255a3"/><path d="M6 30 Q30 40 56 16" stroke="#0255a3" stroke-width="3" fill="none"/><path d="M22 26 L46 14 L50 16 L32 28 Z" fill="#fff"/></svg>
  </div>
  <h3 class="feature-title">Featured Service</h3>
  <p class="feature-copy">nummy nibh ligula pulvinar metus eget consectetuer augue nisi quis lacus Ut ac mi quis lacus mollis aliquam</p>
  <a class="btn-light">Learn More</a>
</article>

<article class="feature" style="left:439px">
  <div class="feature-icon">
    <svg width="52" height="36" viewBox="0 0 52 36"><rect x="8" y="3" width="36" height="24" rx="2" fill="none" stroke="#0255a3" stroke-width="3"/><rect x="2" y="29" width="48" height="4" rx="1" fill="#0255a3"/></svg>
  </div>
  <h3 class="feature-title">Online Booking</h3>
  <p class="feature-copy">nummy nibh ligula pulvinar metus eget consectetuer augue nisi quis lacus Ut ac mi quis lacus mollis aliquam</p>
  <a class="btn-light">Learn More</a>
</article>

<article class="feature" style="left:672px">
  <div class="feature-icon">
    <svg width="40" height="60" viewBox="0 0 40 60"><text x="20" y="46" text-anchor="middle" font-family="Arimo, sans-serif" font-size="50" fill="none" stroke="#0255a3" stroke-width="2">$</text></svg>
  </div>
  <h3 class="feature-title">Low Costs</h3>
  <p class="feature-copy">nummy nibh ligula pulvinar metus eget consectetuer augue nisi quis lacus Ut ac mi quis lacus mollis aliquam</p>
  <a class="btn-light">Learn More</a>
</article>

<a class="promo-banner">
  <div class="promo-photo" role="img" aria-label="Tropical beach with sun umbrellas by turquoise water"></div>
  <span class="promo-head">Vacation of a Lifetime</span>
  <span class="promo-sub">Book a slice of paradise</span>
  <div class="promo-side">
    <span class="promo-brand">Staynestly</span>
    <span class="promo-btn">Book now</span>
  </div>
</a>

<div class="partners">
  <div class="partner"><span class="partner-mark"></span>Brightpeak Labs</div>
  <div class="partner partner-red">Nomad Crest Tours</div>
</div>

<footer class="site-footer">
  <p class="copyright">© 2015 Company Name &nbsp;All right reserved &nbsp;Term of Use</p>
  <div class="social" aria-label="Social links"><span></span><span></span><span></span><span></span></div>
</footer>

</body>
</html>
```